Super Greens Label for Supplement Bottle

We want to design a front label for a health supplement bottle. The product is called Meadow Crunch Chews™. This will be a new product so there is no current website for the product. The focus is on supergreens that taste great and deliver support for energy, digestion, and immune defense.
We want it to be modern, vibrant and appealing.
Bottle size: standard size supplement CLEAR bottle size, with white child resistant cap and the label panel dimensions are 3” x 7”. The label should be primarily white and green, with a touch of red; (see color palettes)/it can also ONLY be white and green. See samples attached.
We are only focused on the front of the bottle design, not on the back, but leave space for the supplement panel and other text on the back.
So the text for the front of the bottle is:
RT Halvorsen's
Meadow Crunch Chews™
Super Greens Blend for:
Energy, Digestion, and Immune Support*
60 Gummies | Dietary Supplement
Raspberry Flavor Gummies
Off to side of the label:
Non-GMO
Vegan Friendly
Plant-Based
Gelatin Free
Colors
Designer to choose colors to be used in the design.
Look and feel
Each slider illustrates characteristics of the customer's brand and the style your logo design should communicate.

```html
<!DOCTYPE html>
<html lang="en">
<head>
<meta charset="utf-8">
<title>Meadow Crunch Chews – Front Label</title>
<link href="https://fonts.googleapis.com/css2?family=Lexend:wght@400;600;700&display=swap" rel="stylesheet">
<style>
  :root {
    --page: #ffffff;
    --green: #2e7d57;
    --green-deep: #28704d;
    --green-light: #5fa383;
    --white: #ffffff;
    --raspberry: #d8455a;
  }
  html, body {
    margin: 0;
    width: 1200px;
    height: 1200px;
    overflow: hidden;
    background: var(--page);
    font-family: "Lexend", sans-serif;
  }
  .label {
    position: absolute;
    left: 150px;
    top: 72px;
    width: 900px;
    height: 1056px;
    background: radial-gradient(ellipse at 55% 45%, var(--green-light) 0%, var(--green) 55%, var(--green-deep) 100%);
    color: var(--white);
    overflow: hidden;
  }
  .label__stripe {
    position: absolute;
    top: 0;
    bottom: 0;
    width: 20px;
    background: var(--white);
  }
  .label__stripe--left { left: 70px; }
  .label__stripe--right { right: 72px; }
  .brand {
    position: absolute;
    top: 196px;
    left: 90px;
    right: 92px;
    font-size: 44px;
    font-weight: 400;
    letter-spacing: 1px;
    display: flex;
    justify-content: center;
    align-items: center;
    gap: 14px;
    white-space: nowrap;
  }
  .brand__dot {
    width: 16px;
    height: 16px;
    border-radius: 50%;
    background: var(--white);
  }
  .product-name {
    position: absolute;
    top: 348px;
    left: 90px;
    right: 92px;
    margin: 0;
    text-align: center;
    font-weight: 700;
    font-size: 78px;
    line-height: 108px;
    letter-spacing: -1px;
    white-space: nowrap;
  }
  .benefits {
    position: absolute;
    top: 634px;
    left: 135px;
    width: 638px;
    height: 48px;
    background: var(--white);
    color: var(--green);
    font-weight: 600;
    font-size: 25px;
    display: flex;
    align-items: center;
    justify-content: center;
    white-space: nowrap;
  }
  .claims {
    position: absolute;
    top: 728px;
    left: 0;
    right: 0;
    margin: 0;
    padding: 0;
    list-style: none;
    text-align: center;
    font-size: 22px;
  }
  .claims li { line-height: 32px; }
  .claims li + li::before {
    content: "";
    display: block;
    width: 130px;
    height: 3px;
    margin: 6px auto 8px;
    background: var(--white);
    border-radius: 2px;
    opacity: 0.9;
  }
  .count {
    position: absolute;
    top: 868px;
    left: 135px;
  }
  .count__number {
    font-size: 56px;
    font-weight: 600;
    line-height: 56px;
  }
  .count__unit {
    font-size: 14px;
    line-height: 16px;
  }
  .count__type {
    font-size: 22px;
    margin-top: 6px;
  }
  .flavor-badge {
    position: absolute;
    left: 690px;
    top: 875px;
    width: 100px;
    height: 100px;
  }
</style>
</head>
<body>
  <main class="label">
    <div class="label__stripe label__stripe--left"></div>
    <div class="label__stripe label__stripe--right"></div>

    <div class="brand"><span class="brand__dot"></span>RT Halvorsen's</div>

    <h1 class="product-name">Meadow Crunch<br>Chews™</h1>

    <div class="benefits">Energy, Digestion, and Immune Support*</div>

    <ul class="claims">
      <li>non-gmo</li>
      <li>vegan friendly</li>
      <li>plant-based</li>
      <li>gelatin free</li>
    </ul>

    <div class="count">
      <div class="count__number">60</div>
      <div class="count__unit">Gummies</div>
      <div class="count__type">Dietary Supplement</div>
    </div>

    <svg class="flavor-badge" viewBox="0 0 100 100">
      <defs>
        <path id="badge-ring" d="M50,50 m-38,0 a38,38 0 1,1 76,0 a38,38 0 1,1 -76,0"/>
      </defs>
      <circle cx="50" cy="50" r="49" fill="var(--white)"/>
      <circle cx="50" cy="50" r="22" fill="var(--raspberry)" role="img" aria-label="Raspberry fruit illustration"/>
      <text font-family="Lexend, sans-serif" font-size="10" fill="var(--green-deep)">
        <textPath href="#badge-ring" startOffset="2%">Raspberry Flavor Gummies •</textPath>
      </text>
    </svg>
  </main>
</body>
</html>
```